New letter head for Air Conditioning business

We need a new professional letter head design to suit our new re-branded air conditioning business. Our new logo is attached

```html
<!DOCTYPE html>
<html lang="en">
<head>
<meta charset="utf-8">
<title>Norwind Letterhead</title>
<link href="https://fonts.googleapis.com/css2?family=Lato:wght@300;400;700&family=Pinyon+Script&display=swap" rel="stylesheet">
<style>
  :root {
    --backdrop: #e6e6e6;
    --paper: #f3f3f3;
    --ink: #2b2b2b;
    --body-text: #555555;
    --charcoal: #3a3b3d;
    --green: #5cb87f;
    --white: #ffffff;
  }
  * { margin: 0; padding: 0; box-sizing: border-box; }
  html, body {
    width: 1200px; height: 1200px; overflow: hidden;
    background: var(--backdrop);
    font-family: 'Lato', sans-serif;
  }
  .letterhead {
    position: absolute; left: 190px; top: 20px;
    width: 820px; height: 1160px;
    background: var(--paper);
    box-shadow: 0 2px 10px rgba(0,0,0,0.12);
  }
  .brand {
    position: absolute; left: 62px; top: 48px;
    display: flex; align-items: center; gap: 12px;
  }
  .brand-dot { width: 34px; height: 34px; border-radius: 50%; background: var(--green); }
  .brand-name {
    font-weight: 700; font-size: 34px; letter-spacing: 3px;
    color: var(--ink); line-height: 1;
  }
  .contact {
    position: absolute; left: 569px; top: 52px;
    border-left: 1.5px solid var(--green);
    padding-left: 12px;
    font-size: 13px; color: var(--ink); line-height: 17px;
  }
  .contact-row { display: flex; align-items: center; gap: 6px; }
  .contact-row svg { width: 10px; height: 10px; flex: none; }
  .letter {
    position: absolute; left: 88px; top: 274px; width: 644px;
    color: var(--body-text); font-weight: 300; font-size: 13px; line-height: 19.3px;
  }
  .letter-date { margin-bottom: 19px; }
  .recipient-name { font-weight: 700; color: #111; }
  .salutation { margin-top: 38px; margin-bottom: 19px; }
  .letter p.body { text-align: justify; margin-bottom: 19px; }
  .closing { margin-top: 38px; }
  .signature {
    font-family: 'Pinyon Script', cursive;
    font-size: 27px; color: var(--ink); font-weight: 400;
    margin-top: 2px; margin-left: 6px;
  }
  .footer-band {
    position: absolute; left: 0; top: 1111px; width: 689px; height: 30px;
    background: var(--charcoal);
    color: var(--white); font-size: 13px; line-height: 30px;
    text-align: center; padding-left: 10px;
  }
  .footer-accent {
    position: absolute; left: 730px; top: 1111px; width: 90px; height: 30px;
    background: var(--green);
  }
</style>
</head>
<body>
  <main class="letterhead">
    <header>
      <div class="brand">
        <span class="brand-dot"></span>
        <span class="brand-name">NORWIND</span>
      </div>
      <div class="contact">
        <div class="contact-row">
          <svg viewBox="0 0 10 10"><path d="M2 1 L4 3 L3 4 Q4 6 6 7 L7 6 L9 8 L8 9 Q3 9 1 2 Z" fill="none" stroke="#5cb87f" stroke-width="1"/></svg>
          <span>(+1) 555.010.2040</span>
        </div>
        <div class="contact-row">
          <svg viewBox="0 0 10 10"><rect x="1" y="2.5" width="8" height="5.5" fill="#5cb87f"/><path d="M1 2.5 L5 6 L9 2.5" fill="none" stroke="#f3f3f3" stroke-width="0.8"/></svg>
          <span>info@norwindcooling.com</span>
        </div>
        <div class="contact-row">
          <svg viewBox="0 0 10 10"><circle cx="5" cy="5" r="4" fill="none" stroke="#5cb87f" stroke-width="1"/><ellipse cx="5" cy="5" rx="1.8" ry="4" fill="none" stroke="#5cb87f" stroke-width="0.8"/><line x1="1" y1="5" x2="9" y2="5" stroke="#5cb87f" stroke-width="0.8"/></svg>
          <span>www.norwindcooling.com</span>
        </div>
      </div>
    </header>

    <section class="letter">
      <p class="letter-date">01 January 2050</p>
      <address class="recipient" style="font-style:normal">
        <div class="recipient-name">Company (Pvt) Ltd.</div>
        <div>PO Box 3355 Mainville St</div>
        <div>Sample City Country 3355</div>
      </address>
      <p class="salutation">Dear Daniel Marlow,</p>
      <p class="body">Lorem ipsum dolor sit amet, consectetuer adipiscing elit, sed diam nonummy nibh euismod tincidunt ut laoreet dolore magna aliquam erat volutpat. Ut wisi enim ad minim veniam, quis nostrud exerci tation ullamcorper suscipit lobortis nisl ut aliquip ex ea commodo consequat. Duis dolore te feugait nulla facilisi. Nam liber tempor cum soluta nobis eleifend option congue nihil imperdiet doming id quod mazim placerat facer possim assum. Lorem ipsum dolor sit amet, consectetuer adipiscing elit, sed diam nonummy nibh euismod tincidunt ut laoreet dolore magna aliquam erat volutpat. Ut wisi enim ad minim veniam, quis nostrud exerci tation ullamcorper suscipit lobortis nisl ut aliquip ex ea commodo consequat.</p>
      <p class="body">Consectetuer adipiscing elit, sed diam nonummy nibh euismod tincidunt ut laoreet dolore magna aliquam erat volutpat. Ut wisi enim ad minim veniam, quis nostrud exerci tation ullamcorper suscipit lobortis nisl ut aliquip ex ea commodo consequat. Consectetuer adipiscing elit, sed diam nonummy nibh euismod tincidunt ut laoreet dolore magna aliquam erat volutpat. Ut wisi enim ad minim veniam, quis nostrud exerci tation ullamcorper suscipit lobortis nisl ut aliquip ex ea commodo consequat.</p>
      <p class="body">Consectetuer adipiscing elit, sed diam nonummy nibh euismod tincidunt ut laoreet dolore magna aliquam erat volutpat. Ut wisi enim ad minim veniam, quis nostrud exerci tation ullamcorper suscipit lobortis nisl ut aliquip ex ea commodo consequat. Consectetuer adipiscing elit, sed diam nonummy nibh euismod tincidunt ut laoreet dolore magna aliquam erat volutpat. Ut wisi enim ad minim veniam, quis nostrud exerci tation ullamcorper suscipit lobortis nisl ut aliquip ex ea commodo consequat.</p>
      <p class="closing">Sincerely Yours</p>
      <p class="signature">Thomas Avery Lindell</p>
    </section>

    <footer>
      <div class="footer-band">Unit 14, Block B, Harlow Rd, NSW, Australia 2000</div>
      <div class="footer-accent"></div>
    </footer>
  </main>
</body>
</html>
```